Business card design

I need my logo on this card, things I need the card to have on it
licensed and insured.
owner operators Milo & Trent Halvorsen
my phone number 5083716254
Disaster Recovery, Storm Damage Restoration, Proactive Disaster Plan Management, Roof Repair/Restoration Structural Repair and Reconstruction, Emergency Boarding and Tarping Service, Perimeter Fencing, Emergency Tree Removal,

```html
<!DOCTYPE html>
<html lang="en">
<head>
<meta charset="utf-8">
<title>Halvorsen's Construction – Business Card</title>
<link rel="stylesheet" href="https://fonts.googleapis.com/css2?family=Montserrat:wght@400;500&family=Nunito:wght@400;600&display=swap">
<style>
  :root {
    --bg: #9a9a9a;
    --card: #ffffff;
    --brand-blue: #3d8fd1;
    --ink: #231f20;
    --white: #ffffff;
  }
  * { margin: 0; padding: 0; box-sizing: border-box; }
  html, body { width: 1093px; height: 1200px; overflow: hidden; }
  body { background: var(--bg); font-family: "Nunito", sans-serif; color: var(--ink); position: relative; }

  .card {
    position: absolute; left: 262px; width: 585px; height: 362px;
    background: var(--card); border-radius: 22px; overflow: hidden;
  }
  .card--front { top: 223px; }
  .card--back { top: 620px; }

  /* company name block: plain square plus name in the text font */
  .brand { position: absolute; text-align: center; }
  .brand__mark { display: block; margin: 0 auto; background: var(--brand-blue); }
  .brand__name {
    display: block; font-family: "Nunito", sans-serif; font-weight: 600;
    color: var(--brand-blue); line-height: 1.2;
  }

  .card--front .brand { left: 0; right: 0; top: 40px; }
  .card--front .brand__mark { width: 70px; height: 70px; margin-bottom: 28px; }
  .card--front .brand__name { font-size: 26px; }

  .services-title {
    position: absolute; left: 0; right: 0; top: 224px; text-align: center;
    font-family: "Nunito", sans-serif; font-size: 19px; font-weight: 400; line-height: 1;
  }
  .services-title span { display: inline-block; padding: 0 4px 6px; border-bottom: 1.5px solid var(--brand-blue); }

  .services {
    position: absolute; left: 0; right: 0; top: 264px; height: 76px;
    background: var(--brand-blue); color: var(--white);
    font-size: 14.4px; text-align: center; padding-top: 3px;
  }
  .services__row { display: block; height: 25px; line-height: 25px; white-space: nowrap; }
  .services__row span::before { content: "\25CF"; font-size: 9px; margin: 0 4px 0 6px; vertical-align: 2px; }

  /* back */
  .card--back .brand { left: 40px; width: 228px; top: 128px; }
  .card--back .brand__mark { width: 62px; height: 62px; margin-bottom: 20px; }
  .card--back .brand__name { font-size: 21px; }

  .divider { position: absolute; left: 285px; top: 105px; width: 1.5px; height: 176px; background: var(--brand-blue); }

  .contact { position: absolute; left: 298px; top: 103px; width: 280px; }
  .contact__names { font-family: "Montserrat", sans-serif; font-size: 22px; color: var(--brand-blue); font-weight: 400; line-height: 1.2; white-space: nowrap; }
  .contact__role { font-family: "Montserrat", sans-serif; font-size: 12.5px; margin-top: 3px; }
  .contact__licence { font-family: "Montserrat", sans-serif; font-size: 11.5px; color: var(--brand-blue); margin-top: 2px; }
  .contact__address { font-size: 13.5px; line-height: 16px; margin-top: 10px; }
  .contact__list { list-style: none; margin-top: 9px; font-family: "Montserrat", sans-serif; font-size: 13px; }
  .contact__list li { display: flex; align-items: center; height: 23px; }
  .contact__list svg { width: 14px; height: 14px; margin-right: 9px; fill: var(--brand-blue); flex: none; }
</style>
</head>
<body>

<section class="card card--front">
  <div class="brand">
    <span class="brand__mark"></span>
    <span class="brand__name">Halvorsen's Construction LLC</span>
  </div>
  <h2 class="services-title"><span>OUR SERVICES</span></h2>
  <div class="services">
    <p class="services__row"><span>Disaster Recovery</span><span>Storm Damage Restoration</span><span>Proactive Disaster Plan Management</span></p>
    <p class="services__row"><span>Roof Repair/Restoration Structural Repair and Reconstruction</span><span>Perimeter Fencing</span></p>
    <p class="services__row"><span>Emergency Boarding and Tarping Service</span><span>Emergency Tree Removal</span></p>
  </div>
</section>

<section class="card card--back">
  <div class="brand">
    <span class="brand__mark"></span>
    <span class="brand__name">Halvorsen's Construction LLC</span>
  </div>
  <div class="divider"></div>
  <div class="contact">
    <p class="contact__names">Milo &amp; Trent Halvorsen</p>
    <p class="contact__role">owner operators</p>
    <p class="contact__licence">Licensed and insured</p>
    <p class="contact__address">48 Cedar Ridge Lane<br>Brandon, MS 39042</p>
    <ul class="contact__list">
      <li>
        <svg viewBox="0 0 16 16" aria-hidden="true"><path d="M1 5c0-2 3-3 7-3s7 1 7 3v1h-3V4.5c-1-.5-2.5-.7-4-.7s-3 .2-4 .7V6H1z"/><path d="M4 7l1-2h6l1 2 2 2v5H2V9zm4 1.2a2 2 0 100 4 2 2 0 000-4z"/></svg>
        <span>5083716254</span>
      </li>
      <li>
        <svg viewBox="0 0 16 16" aria-hidden="true"><path d="M1 3h14v1.5L8 9 1 4.5z"/><path d="M1 6.3l7 4.5 7-4.5V13H1z"/></svg>
        <span>info@halvorsenbuild.com</span>
      </li>
      <li>
        <svg viewBox="0 0 16 16" aria-hidden="true"><path d="M8 1a7 7 0 100 14A7 7 0 008 1zm0 1.5c.6 0 1 .3 1.6.8L8.5 5 6.7 4.4 5.5 6l1.3 1.5-.5 2L4 8.3l-1-1.8A5.5 5.5 0 018 2.5zm2.5 5l2.8.6a5.5 5.5 0 01-3.6 4.5l-.5-2.1z"/></svg>
        <span>www.halvorsenbuild.com</span>
      </li>
    </ul>
  </div>
</section>

</body>
</html>
```